Yard sign design for high end luxury home builder.

Need a design for signage on custom homes that are being built. I already have a logo that I am satisfied with that needs to be incorporated. I need the following incorporated in the design of the sign-
- Lic number 381526
- phone number (805) 555-0148‬
- quennbuilderscrew.com
- Logo/Branding

If possible it may be nice to have the following quote that is on are business cards-

Quote from Gerard of Norvelle-
HE WHO WORKS WITH HIS HANDS IS A LABORER.
HE WHO WORKS WITH HIS HANDS & HIS HEAD IS A CRAFTSMAN.
HE WHO WORKS WITH HIS HANDS & HIS HEAD & HIS HEART IS AN ARTISAN.
-GERARD OF NORVELLE

Target Market(s)

Archetect, Designers, Clients desiring to build a new home or remodel.

Colors
fde9d4
fee4d5
fabb94
fac994
faa54b
f68d4d
f37122
f78f20
f68e4e

Requirements
Must have
• - Lic number 381526
• - phone number (805) 555-0148‬
• - quennbuilderscrew.com
• - Logo/Branding
Nice to have
• Quote from Gerard of Norvelle-
• HE WHO WORKS WITH HIS HANDS IS A LABORER.
• HE WHO WORKS WITH HIS HANDS & HIS HEAD IS A CRAFTSMAN.
• HE WHO WORKS WITH HIS HANDS & HIS HEAD & HIS HEART IS AN ARTISAN.
• -GERARD OF NORVELLE
• OR the below statement-
• Craftsmen that Care
Should not have
• Any additional verbiage not specified above including any type of verbiage about what kind of company we are. For instance- Integrity, reputable... It's just all played out. Im just looking for a bitching design that has the info that compliments my logo/branding.

```html
<!DOCTYPE html>
<html lang="en">
<head>
<meta charset="utf-8">
<title>Quenn Builders Crew – Yard Sign</title>
<link rel="stylesheet" href="https://fonts.googleapis.com/css2?family=PT+Serif:wght@400;700&display=swap">
<style>
  :root {
    --page: #ffffff;
    --ink-dark: #1f1d1b;
    --paper-light: #eceeed;
    --tan: #a08a6e;
    --tan-deep: #8c7658;
    --quote-on-dark: #a8957c;
    --quote-on-light: #9a8468;
    --pill-text: #f3efe9;
  }
  * { box-sizing: border-box; margin: 0; padding: 0; }
  html, body {
    width: 1200px; height: 1200px; overflow: hidden;
    background: var(--page);
    font-family: "PT Serif", Georgia, serif;
  }
  .board { position: relative; width: 1200px; height: 1200px; }

  .sign {
    position: absolute; top: 246px; width: 523px; height: 696px;
    background: var(--ink-dark); color: var(--tan);
  }
  .sign--dark { left: 58px; }
  .sign--light { left: 611px; background: var(--paper-light); }

  .sign__frame {
    position: absolute; inset: 8px; border: 1.5px solid var(--tan);
  }
  .sign__headline {
    position: absolute; top: 34px; left: 0; right: 0;
    text-align: center; font-size: 44px; font-weight: 400; letter-spacing: 0.2px;
  }
  .brand {
    position: absolute; top: 150px; left: 30px; right: 30px;
    text-align: center; font-size: 50px; font-weight: 700;
    line-height: 1.15; text-transform: uppercase; letter-spacing: 2px;
    color: var(--tan);
  }
  .sign__phone {
    position: absolute; top: 432px; left: 0; right: 0;
    text-align: center; font-size: 61px; line-height: 1; letter-spacing: -0.5px;
  }
  .divider {
    position: absolute; top: 508px; left: 54px; right: 54px; height: 30px;
  }
  .divider__line {
    position: absolute; top: 15px; height: 1px; width: 44%; background: var(--tan);
  }
  .divider__line--left { left: 0; }
  .divider__line--right { right: 0; }
  .divider__mark {
    position: absolute; left: 50%; top: -2px; transform: translateX(-50%);
    font-size: 32px; font-weight: 700; line-height: 1;
  }
  .quote {
    position: absolute; top: 545px; left: 0; right: 0;
    text-align: center; font-size: 13.5px; line-height: 18px;
    color: var(--quote-on-dark);
  }
  .sign--light .quote { color: var(--quote-on-light); }
  .quote strong { font-weight: 700; color: var(--tan); }
  .quote__rule {
    position: absolute; top: 607px; left: 50%; width: 180px; margin-left: -90px;
    height: 1px; background: var(--tan);
  }
  .quote__author {
    position: absolute; top: 616px; left: 0; right: 0;
    text-align: center; font-size: 13px; font-weight: 700;
  }
  .sign__web {
    position: absolute; top: 648px; left: 98px; width: 324px; height: 40px;
    background: var(--tan); color: var(--ink-dark);
    border-radius: 16px 16px 0 0;
    display: flex; align-items: center; justify-content: center;
    font-size: 24px; letter-spacing: 0.3px;
  }
  .sign--light .sign__web { color: var(--pill-text); }
  .sign__licence {
    position: absolute; top: 666px; right: 26px; font-size: 10px;
  }
</style>
</head>
<body>
<main class="board">

  <section class="sign sign--dark">
    <div class="sign__frame"></div>
    <h1 class="sign__headline">Craftsmen That Care</h1>
    <p class="brand">Quenn Builders<br>Crew Inc.</p>
    <p class="sign__phone">(805) 555 0148</p>
    <div class="divider">
      <span class="divider__line divider__line--left"></span>
      <span class="divider__mark">&ldquo;</span>
      <span class="divider__line divider__line--right"></span>
    </div>
    <blockquote class="quote">
      He who works with his hands is a <strong>laborer</strong>.<br>
      He who works with his hands &amp; his head is a <strong>craftsman</strong>.<br>
      He who works with his hands &amp; his head &amp; his heart is an <strong>artisan</strong>.
    </blockquote>
    <span class="quote__rule"></span>
    <p class="quote__author">Gerard of Norvelle</p>
    <p class="sign__web">quennbuilderscrew.com</p>
    <p class="sign__licence">Lic 381526</p>
  </section>

  <section class="sign sign--light">
    <div class="sign__frame"></div>
    <h1 class="sign__headline">Craftsmen That Care</h1>
    <p class="brand">Quenn Builders<br>Crew Inc.</p>
    <p class="sign__phone">(805) 555 0148</p>
    <div class="divider">
      <span class="divider__line divider__line--left"></span>
      <span class="divider__mark">&ldquo;</span>
      <span class="divider__line divider__line--right"></span>
    </div>
    <blockquote class="quote">
      He who works with his hands is a <strong>laborer</strong>.<br>
      He who works with his hands &amp; his head is a <strong>craftsman</strong>.<br>
      He who works with his hands &amp; his head &amp; his heart is an <strong>artisan</strong>.
    </blockquote>
    <span class="quote__rule"></span>
    <p class="quote__author">Gerard of Norvelle</p>
    <p class="sign__web">quennbuilderscrew.com</p>
    <p class="sign__licence">Lic 381526</p>
  </section>

</main>
</body>
</html>
```